Residential Remodeling Contractor needs updated business card

I need a new design for my business card.
Name of the company is Ridgefell Construction. I need a card that commands presence, strength, integrity. I have been in business for 28 years. I am a Residential Remodeling Contractor that covers all aspects of a residential remodel and build.

```html
<!DOCTYPE html>
<html lang="en">
<head>
<meta charset="utf-8">
<title>Ridgefell Construction – Business Card</title>
<link href="https://fonts.googleapis.com/css2?family=Cinzel:wght@600&family=Arimo:wght@400&display=swap" rel="stylesheet">
<style>
  :root {
    --navy: #1b3f7f;
    --navy-deep: #14306a;
    --white: #ffffff;
    --stage: #3b3d40;
    --rule: rgba(255,255,255,0.85);
  }
  * { box-sizing: border-box; margin: 0; padding: 0; }
  html, body { width: 1200px; height: 901px; overflow: hidden; }
  body { background: var(--stage); position: relative; font-family: "Arimo", Arial, sans-serif; }

  .card {
    position: absolute;
    width: 560px; height: 320px;
    border-radius: 22px;
    overflow: hidden;
    background: var(--navy);
  }
  .card--front { left: 50px; top: 110px; }
  .card--back  { left: 590px; top: 470px; }

  .brand {
    position: absolute;
    display: flex; align-items: center; gap: 16px;
    font-family: "Cinzel", Georgia, serif;
    font-weight: 600;
    line-height: 1.05;
    letter-spacing: 0.02em;
    white-space: nowrap;
  }
  .brand__mark { width: 14px; height: 14px; border-radius: 50%; background: currentColor; flex: none; }
  .brand__name { display: block; }
  .card--front .brand { color: var(--white); font-size: 46px; left: 92px; top: 108px; }
  .card--back .brand { color: var(--navy); font-size: 21px; left: 318px; top: 124px; gap: 9px; letter-spacing: 0.01em; }
  .card--back .brand__mark { width: 9px; height: 9px; }

  .back-shape { position: absolute; inset: 0; }

  .contact { position: absolute; left: 34px; top: 58px; color: var(--white); width: 222px; }
  .contact__name { font-family: "Cinzel", Georgia, serif; font-weight: 600; font-size: 17px; letter-spacing: 0.02em; white-space: nowrap; }
  .contact__title { font-size: 13px; margin-top: 2px; }
  .contact__rule { height: 1px; background: var(--rule); margin: 12px 0; }
  .contact__address { font-size: 13px; line-height: 1.45; }
  .contact__list { list-style: none; font-size: 13px; line-height: 1.7; }
  .contact__list li { display: flex; align-items: center; gap: 8px; white-space: nowrap; }
  .contact__list svg { width: 12px; height: 12px; flex: none; fill: var(--white); }
</style>
</head>
<body>

  <section class="card card--front" aria-label="Card front">
    <div class="brand">
      <span class="brand__mark"></span>
      <span class="brand__name">Ridgefell<br>Construction</span>
    </div>
  </section>

  <section class="card card--back" aria-label="Card back">
    <svg class="back-shape" viewBox="0 0 560 320" aria-hidden="true">
      <defs>
        <linearGradient id="arcShade" x1="0" y1="0" x2="1" y2="1">
          <stop offset="0" stop-color="#ffffff"/>
          <stop offset="0.55" stop-color="#6f86b8"/>
          <stop offset="1" stop-color="#1b3f7f"/>
        </linearGradient>
      </defs>
      <circle cx="628" cy="56" r="372" fill="url(#arcShade)"/>
      <circle cx="632" cy="52" r="364" fill="var(--navy)"/>
      <circle cx="640" cy="50" r="360" fill="var(--white)"/>
    </svg>

    <div class="brand">
      <span class="brand__mark"></span>
      <span class="brand__name">Ridgefell<br>Construction</span>
    </div>

    <div class="contact">
      <p class="contact__name">DANIEL WHITCOMBE</p>
      <p class="contact__title">Owner &amp; Manager</p>
      <div class="contact__rule"></div>
      <p class="contact__address">P.O. Box&nbsp; Street Name<br>Country Name AB, A5B 521</p>
      <div class="contact__rule"></div>
      <ul class="contact__list">
        <li><svg viewBox="0 0 12 12"><path d="M1 4c0-2 2-3 5-3s5 1 5 3l-2 1-1-2H4L3 5zM2 6h8l1 5H1z"/></svg>555 310 4418</li>
        <li><svg viewBox="0 0 12 12"><path d="M3 0h6v12H3zM4 1v9h4V1z"/></svg>555-207-66341</li>
        <li><svg viewBox="0 0 12 12"><path d="M0 2h12v8H0zM1 3l5 4 5-4v-0.2H1z"/></svg>info@ridgefellconstruction.com</li>
        <li><svg viewBox="0 0 12 12"><circle cx="6" cy="6" r="5.5"/></svg>www.ridgefellconstruction.com</li>
      </ul>
    </div>
  </section>

</body>
</html>
```